Custom Office Whiteboard for Staff

I need a custom whiteboard layout design. All fields are contained in the attached images along with artwork requirements including required bleed. Size will be 1200mm x 900mm.

Feel free to make is more visually appealing than this draft.

Use colors blue, black and white to keep company feel.

Font styles to use
Sans Serif

Colors
ffffff
000000
33a6d7

```html
<!DOCTYPE html>
<html lang="en">
<head>
<meta charset="utf-8">
<title>Skyward Ballooning – Staff Whiteboard</title>
<link href="https://fonts.googleapis.com/css2?family=Catamaran:wght@400;500;600&display=swap" rel="stylesheet">
<style>
:root{
  --blue:#12a9e6;
  --black:#000000;
  --white:#ffffff;
  --charcoal:#3c3c3c;
  --header-grey:#f3f3f3;
  --rule:#c9c9c9;
  --ink:#111111;
}
*{box-sizing:border-box;margin:0;padding:0}
html,body{width:1200px;height:918px;overflow:hidden;background:var(--white)}
body{font-family:"Catamaran",sans-serif;color:var(--ink);position:relative}
.board{position:absolute;inset:0;width:1200px;height:918px;background:var(--white);overflow:hidden}
.header-art{position:absolute;left:0;top:0}
.brand{position:absolute;left:100px;top:74px;display:flex;align-items:center;gap:12px;font-size:40px;font-weight:600;color:var(--black);letter-spacing:.5px}
.brand-dot{width:22px;height:22px;border-radius:50%;background:var(--blue)}
.contacts{position:absolute;left:553px;top:56px;list-style:none;font-size:20px;line-height:31.5px}
.contacts li{display:flex;align-items:center;gap:10px}
.contacts svg{width:17px;height:17px;flex:none}
.company{position:absolute;left:900px;top:58px;font-size:19px;line-height:27px}
.company .gap{margin-top:4px}
.grid{position:absolute;border-collapse:collapse;table-layout:fixed;background:var(--white)}
.grid caption{background:var(--blue);color:var(--white);font-weight:500;text-transform:uppercase;letter-spacing:.3px}
.grid th{background:var(--charcoal);color:var(--white);font-weight:500;border-right:1px solid #666;line-height:1}
.grid th:last-child{border-right:none}
.grid td{border:1px solid var(--rule);text-align:center}
.crew{left:67px;top:195px;width:787px}
.crew caption{height:40px;line-height:42px;font-size:23px}
.crew th{height:36px;font-size:14px}
.crew td{height:29.7px}
.notes{position:absolute;left:889px;top:195px;width:258px;height:432px;border:3px solid var(--rule);border-top:none;border-radius:0 0 6px 6px}
.notes-title{position:relative;height:57px;margin:0 -3px;background:var(--blue);color:var(--white);font-size:33px;font-weight:500;text-align:center;line-height:62px}
.notes-title::after{content:"";position:absolute;left:50%;bottom:-11px;margin-left:-13px;border:13px solid transparent;border-bottom:none;border-top:11px solid var(--blue)}
.small caption{height:25px;line-height:27px;font-size:15px}
.small th{height:25px;font-size:14px}
.small td{height:24.2px;font-size:11px}
.six{left:67px;top:647px;width:266px}
.twelve{left:351px;top:647px;width:265px}
.balloons{left:634px;top:647px;width:513px}
.footer{position:absolute;left:0;bottom:0}
</style>
</head>
<body>
<main class="board">
  <svg class="header-art" width="1200" height="180" viewBox="0 0 1200 180" aria-hidden="true">
    <rect x="0" y="0" width="1200" height="24" fill="var(--header-grey)"/>
    <polygon points="0,0 522,0 522,24 425,156 420,180 0,180" fill="var(--header-grey)"/>
    <polygon points="515,24 530,24 433,156 418,156" fill="var(--blue)"/>
  </svg>

  <div class="brand"><span class="brand-dot"></span>Skyward Ballooning</div>

  <ul class="contacts">
    <li><svg viewBox="0 0 18 18"><rect x="1.5" y="4" width="15" height="10" fill="none" stroke="#4aa3d8" stroke-width="1.3"/><path d="M1.5 4l7.5 6 7.5-6" fill="none" stroke="#4aa3d8" stroke-width="1.3"/></svg>hello@skywardballooning.example</li>
    <li><svg viewBox="0 0 18 18"><circle cx="9" cy="9" r="7.5" fill="none" stroke="#4aa3d8" stroke-width="1.3"/><ellipse cx="9" cy="9" rx="3.2" ry="7.5" fill="none" stroke="#4aa3d8" stroke-width="1.1"/><path d="M1.5 9h15M3 5h12M3 13h12" stroke="#4aa3d8" stroke-width="1.1"/></svg>www.skywardballooning.example</li>
    <li><svg viewBox="0 0 18 18"><circle cx="9" cy="9" r="7.5" fill="none" stroke="#4aa3d8" stroke-width="1.3"/><path d="M6.3 5.2l1.4 2.1-.9 1.1c.6 1.2 1.5 2.1 2.7 2.7l1.1-.9 2.1 1.4-.7 1.4c-3.3-.2-6.1-3-6.3-6.3z" fill="#4aa3d8"/></svg>1300 555 019</li>
  </ul>

  <div class="company">
    <p>Southern Aerostat Co Pty Ltd</p>
    <p>T/A Skyward Ballooning</p>
    <p class="gap">CASA AOC: S000418</p>
    <p>Certificate of Approval: 5108</p>
  </div>

  <table class="grid crew">
    <caption>Flight / Ground Crew</caption>
    <thead><tr><th>Crew Name</th><th>License Class</th><th>Medical</th><th>BFR</th><th>Instructor<br>Rating</th><th>CAO 20.11</th><th>DAMP</th><th>Maintenance<br>Authority</th><th>ASIC</th></tr></thead>
    <tbody>
      <tr><td></td><td></td><td></td><td></td><td></td><td></td><td></td><td></td><td></td></tr>
      <tr><td></td><td></td><td></td><td></td><td></td><td></td><td></td><td></td><td></td></tr>
      <tr><td></td><td></td><td></td><td></td><td></td><td></td><td></td><td></td><td></td></tr>
      <tr><td></td><td></td><td></td><td></td><td></td><td></td><td></td><td></td><td></td></tr>
      <tr><td></td><td></td><td></td><td></td><td></td><td></td><td></td><td></td><td></td></tr>
      <tr><td></td><td></td><td></td><td></td><td></td><td></td><td></td><td></td><td></td></tr>
      <tr><td></td><td></td><td></td><td></td><td></td><td></td><td></td><td></td><td></td></tr>
      <tr><td></td><td></td><td></td><td></td><td></td><td></td><td></td><td></td><td></td></tr>
      <tr><td></td><td></td><td></td><td></td><td></td><td></td><td></td><td></td><td></td></tr>
      <tr><td></td><td></td><td></td><td></td><td></td><td></td><td></td><td></td><td></td></tr>
      <tr><td></td><td></td><td></td><td></td><td></td><td></td><td></td><td></td><td></td></tr>
      <tr><td></td><td></td><td></td><td></td><td></td><td></td><td></td><td></td><td></td></tr>
    </tbody>
  </table>

  <section class="notes"><h2 class="notes-title">NOTES</h2></section>

  <table class="grid small six">
    <caption>6 Monthly Tasks</caption>
    <colgroup><col style="width:153px"><col></colgroup>
    <thead><tr><th>Task</th><th>Due Date</th></tr></thead>
    <tbody>
      <tr><td>Operations Manual</td><td></td></tr>
      <tr><td>Staff Meeting</td><td></td></tr>
      <tr><td>SMS Meeting</td><td></td></tr>
      <tr><td>Fire Extinguisher Inspection</td><td></td></tr>
      <tr><td>Flight Instrument Inspection</td><td></td></tr>
      <tr><td></td><td></td></tr><tr><td></td><td></td></tr><tr><td></td><td></td></tr>
    </tbody>
  </table>

  <table class="grid small twelve">
    <caption>12 Monthly Tasks</caption>
    <colgroup><col style="width:132px"><col></colgroup>
    <thead><tr><th>Task</th><th>Due Date</th></tr></thead>
    <tbody>
      <tr><td>COA Internal Audit</td><td></td></tr>
      <tr><td>SMS Audit</td><td></td></tr>
      <tr><td>Fatigue Training</td><td></td></tr>
      <tr><td>CAO 20.11</td><td></td></tr>
      <tr><td></td><td></td></tr><tr><td></td><td></td></tr><tr><td></td><td></td></tr><tr><td></td><td></td></tr>
    </tbody>
  </table>

  <table class="grid small balloons">
    <caption>Balloon Annual / Periodic Schedule</caption>
    <thead><tr><th>Balloon</th><th>Type</th><th>Annual Date</th><th>Periodic Time</th></tr></thead>
    <tbody>
      <tr><td>VH-QKA</td><td>Aero D90</td><td></td><td></td></tr>
      <tr><td>VH-QKB</td><td>Aero E180</td><td></td><td></td></tr>
      <tr><td>VH-QKC</td><td>Aero E240</td><td></td><td></td></tr>
      <tr><td>VH-QKD</td><td>Aero B400</td><td></td><td></td></tr>
      <tr><td>VH-QKE</td><td>Aero G450</td><td></td><td></td></tr>
      <tr><td></td><td></td><td></td><td></td></tr><tr><td></td><td></td><td></td><td></td></tr><tr><td></td><td></td><td></td><td></td></tr>
    </tbody>
  </table>

  <svg class="footer" width="1200" height="11" viewBox="0 0 1200 11" aria-hidden="true">
    <polygon points="0,0 489,0 481,11 0,11" fill="var(--blue)"/>
    <polygon points="497,0 1200,0 1200,11 489,11" fill="var(--black)"/>
  </svg>
</main>
</body>
</html>
```